PERI VALORE

We need a letterhead design for an Image & Etiquette Consultancy company based in Singapore.

The services we provide are Personal Image Consultation, Image & Etiquette Workshop for schools and corporate.

The design should have our corporate colour as seen in the logo files I have uploaded.

Since our company helps clients with their image, the design should be aesthetically very appealing. It should reflect a very classy & elegant feel.

I will print the letterhead using my printer but most of the time will use it to write letters to my clients therefore the format should include MS Word.

```html
<!DOCTYPE html>
<html lang="en">
<head>
<meta charset="utf-8">
<title>Peri Valore Letterhead</title>
<link href="https://fonts.googleapis.com/css2?family=Michroma&family=Open+Sans:wght@400&display=swap" rel="stylesheet">
<style>
  :root {
    --backdrop: #dfdfdd;
    --paper: #ffffff;
    --plum: #2e1a3d;
    --gold: #c9a227;
    --ink: #3a3340;
  }
  html, body { margin: 0; padding: 0; overflow: hidden; }
  body { width: 1200px; height: 1200px; background: var(--backdrop); position: relative; }
  .letterhead {
    position: absolute; left: 273px; top: 137px; width: 653px; height: 924px;
    background: var(--paper); overflow: hidden;
  }
  .header-band {
    position: absolute; left: 0; top: 0; width: 100%; height: 102px; background: var(--plum);
  }
  .brand-name {
    position: absolute; left: 48px; top: 52px; margin: 0;
    font-family: "Michroma", sans-serif; font-weight: 400; font-size: 22px;
    letter-spacing: 1px; color: var(--gold); line-height: 1;
  }
  .footer-swoosh { position: absolute; left: 0; top: 848px; width: 653px; height: 76px; }
  .company-block {
    position: absolute; right: 200px; top: 834px; text-align: right;
    font-family: "Open Sans", sans-serif; font-size: 9.5px; color: var(--ink); line-height: 16px;
  }
  .company-name {
    font-family: "Michroma", sans-serif; font-size: 13px; color: var(--plum);
    margin: 0 0 2px; line-height: 20px; letter-spacing: 0.3px;
  }
  .company-block p { margin: 0; }
  .contact-list {
    position: absolute; left: 487px; top: 837px; margin: 0; padding: 0; list-style: none;
    font-family: "Open Sans", sans-serif; font-size: 9.5px; color: var(--ink); line-height: 15.5px;
  }
  .contact-list li { display: flex; align-items: center; gap: 6px; }
  .contact-list svg { width: 10px; height: 10px; fill: var(--plum); flex: none; }
</style>
</head>
<body>
  <main class="letterhead">
    <header class="header-band">
      <h1 class="brand-name">PERI VALORE</h1>
    </header>

    <svg class="footer-swoosh" viewBox="0 0 653 76" preserveAspectRatio="none" aria-hidden="true">
      <defs>
        <linearGradient id="goldSweep" x1="0" y1="0" x2="1" y2="0">
          <stop offset="0" stop-color="#a8832f"/>
          <stop offset="0.15" stop-color="#b8912a"/>
          <stop offset="0.22" stop-color="#dcb40c"/>
          <stop offset="0.4" stop-color="#f9f1a6"/>
          <stop offset="0.6" stop-color="#e2c245"/>
          <stop offset="0.8" stop-color="#d2a70a"/>
          <stop offset="1" stop-color="#d9b011"/>
        </linearGradient>
      </defs>
      <path d="M0,5 Q220,30 457,63 Q220,46 0,31 Z" fill="var(--plum)"/>
      <path d="M0,35 Q320,58 653,73 L653,76 L0,76 Z" fill="url(#goldSweep)"/>
    </svg>

    <section class="company-block">
      <h2 class="company-name">Peri Valore Limited</h2>
      <p>Your Long address with code no.</p>
      <p>your licence no.: xxx xxx xxx xx</p>
    </section>

    <ul class="contact-list">
      <li>
        <svg viewBox="0 0 10 10"><path d="M1,3 Q5,0 9,3 L8,4.5 L6.5,3.8 L6.5,3 Q5,2.5 3.5,3 L3.5,3.8 L2,4.5 Z M2.5,5 L7.5,5 L8.5,9 L1.5,9 Z"/></svg>
        <span>000 000 000 000</span>
      </li>
      <li>
        <svg viewBox="0 0 10 10"><path d="M0.5,2 L9.5,2 L5,5.5 Z M0.5,3 L5,6.5 L9.5,3 L9.5,8 L0.5,8 Z"/></svg>
        <span>yourname@perivalore.com</span>
      </li>
      <li>
        <svg viewBox="0 0 10 10"><path d="M5,0.5 A4.5,4.5 0 1 0 5,9.5 A4.5,4.5 0 1 0 5,0.5 Z M5,1.5 Q6.8,3 6.8,5 Q6.8,7 5,8.5 Q3.2,7 3.2,5 Q3.2,3 5,1.5 Z M1.5,4.5 L8.5,4.5 L8.5,5.5 L1.5,5.5 Z" fill-rule="evenodd"/></svg>
        <span>www.perivalore.com</span>
      </li>
    </ul>
  </main>
</body>
</html>
```